Update patient consent forms and contract

Objective
Redesign the existing patient contract information document to create a modern,contempory, and easy-to-understand experience for patients. The updated design should improve readability, accessibility, and overall presentation while maintaining compliance with healthcare and legal requirements.

Key Deliverables

Refreshed visual design and layout
Improved information hierarchy and readability
Modern typography and colour palette aligned with brand guidelines
Clear section headings and navigation
Print-ready and digital versions (PDF)

Include KEV Logo within patient KEV consent to treatment. Ideally this document should be portrait not landscape.
Updates

I would love a front page to be included in the document

```html
<!DOCTYPE html>
<html lang="en">
<head>
<meta charset="utf-8">
<title>Payment Option Selection – Northline Orthodontics</title>
<link href="https://fonts.googleapis.com/css2?family=Outfit:wght@400;500;600;700&family=Roboto:wght@500;700&display=swap" rel="stylesheet">
<style>
  :root {
    --navy: #14324f;
    --blue: #0096d6;
    --icon: #3f7fc4;
    --white: #ffffff;
    --ink: #2b2b2b;
    --grey-band: #eeeeee;
    --stage: #b5b5b5;
    --muted: #9aa2aa;
  }
  * { box-sizing: border-box; margin: 0; padding: 0; }
  html, body { width: 1200px; height: 943px; overflow: hidden; }
  body {
    background: var(--stage);
    font-family: "Outfit", sans-serif;
    display: flex; align-items: center; justify-content: center;
  }
  .sheet {
    position: relative; width: 700px; height: 906px;
    background: var(--white); overflow: hidden;
  }
  .abs { position: absolute; }
  .panel-dark { left: 0; top: 0; width: 700px; height: 604px; background: var(--navy); }
  .title { left: 39px; top: 15px; color: var(--white); font-size: 24px; font-weight: 700; letter-spacing: -0.2px; }
  .partner-mark { left: 360px; top: 36px; display: flex; align-items: center; gap: 8px; color: var(--muted); font-size: 16px; font-weight: 600; }
  .partner-mark .dot { width: 26px; height: 26px; border-radius: 50%; background: var(--muted); }
  .brand-mark { left: 520px; top: 32px; display: flex; align-items: center; gap: 8px; color: var(--muted); font-size: 16px; font-weight: 600; }
  .brand-mark .square { width: 30px; height: 30px; background: var(--blue); }
  .thanks { left: 40px; top: 73px; color: var(--white); font-size: 12px; font-weight: 700; }
  .intro { left: 40px; top: 101px; width: 625px; color: var(--white); font-size: 12px; line-height: 20.4px; }
  .heading { color: var(--blue); font-size: 19px; font-weight: 600; }
  .select-heading { left: 40px; top: 186px; }
  .checkbox { width: 25px; height: 25px; background: var(--white); border: 2px solid var(--blue); border-radius: 2px; }
  .option-label { color: var(--white); font-family: "Roboto", sans-serif; font-weight: 500; font-size: 13.4px; }
  .copy { color: var(--white); font-size: 12px; line-height: 16px; }
  .divider-dashed { left: 40px; top: 351px; width: 612px; border-top: 1px dashed #7f93a7; }
  .important-heading { left: 40px; top: 500px; }
  .declaration-heading { left: 0; top: 608px; width: 700px; text-align: center; }
  .declaration-text { left: 0; top: 637px; width: 700px; text-align: center; color: var(--ink); font-size: 12px; }
  .sign-line { width: 117px; border-top: 1px solid var(--ink); }
  .sign-label { width: 117px; text-align: center; color: var(--ink); font-size: 13.5px; font-weight: 600; }
  .footer-bank { left: 0; top: 783px; width: 225px; height: 123px; background: var(--blue); color: var(--white); }
  .footer-info { left: 225px; top: 783px; width: 475px; height: 123px; background: var(--grey-band); }
  .footer-heading { font-size: 10px; font-weight: 700; }
  .bank-row { position: absolute; left: 41px; font-size: 8.5px; display: flex; }
  .bank-row .key { width: 94px; }
  .bank-row .val { font-weight: 700; }
  .info-heading { left: 23px; top: 14px; color: var(--ink); }
  .info-row { position: absolute; left: 20px; display: flex; align-items: center; gap: 6px; color: var(--ink); font-size: 8.5px; }
  .info-row svg { width: 11px; height: 11px; }
  .footer-divider { left: 229px; top: 16px; height: 87px; border-left: 1px solid #cfcfcf; }
  .doctor { position: absolute; left: 255px; display: flex; gap: 6px; color: var(--ink); font-size: 8.5px; line-height: 10px; }
  .doctor strong { font-weight: 700; display: block; }
  .doctor svg { width: 12px; height: 14px; margin-top: 1px; }
</style>
</head>
<body>
<main class="sheet">
  <section class="panel-dark abs">
    <h1 class="title abs">Payment Option Selection</h1>
    <div class="partner-mark abs"><span class="dot"></span>KEV</div>
    <div class="brand-mark abs"><span class="square"></span>Northline orthodontics</div>

    <p class="thanks abs">Thank you for choosing Northline Orthodontics.</p>
    <p class="intro abs">To assist with managing your treatment fees, please select your preferred payment method below. If you would prefer to pay at each scheduled appointment, please advise our reception team. Please note that appointments are generally scheduled every 6–8 weeks.</p>

    <h2 class="heading select-heading abs">Please select one option:</h2>

    <div class="checkbox abs" style="left:40px;top:220px;"></div>
    <span class="option-label abs" style="left:74px;top:224px;">Credit Card Direct Debit</span>
    <svg class="abs" style="left:311px;top:218px;" width="76" height="54" viewBox="0 0 76 54" fill="none" stroke="var(--icon)" stroke-width="2" stroke-linecap="round">
      <rect x="1" y="1" width="62" height="40" rx="3"/>
      <line x1="1" y1="17" x2="63" y2="17"/><line x1="1" y1="23" x2="63" y2="23"/>
      <line x1="9" y1="9" x2="19" y2="9"/><line x1="9" y1="13" x2="25" y2="13"/>
      <circle cx="62" cy="40" r="12" fill="var(--navy)"/>
      <path d="M56 40h12M63 35l5 5-5 5"/>
    </svg>
    <p class="copy abs" style="left:40px;top:256px;">I would like to pay via credit card direct debit.</p>
    <p class="copy abs" style="left:40px;top:288px;width:625px;">I understand that Northline Orthodontics will send me a secure PayLink payment link to enter my credit card details. The card provided will be securely stored and used as my nominated payment method for future scheduled payments relating to my treatment plan.</p>

    <div class="divider-dashed abs"></div>

    <div class="checkbox abs" style="left:40px;top:368px;"></div>
    <span class="option-label abs" style="left:74px;top:372px;">Monthly Direct Bank Transfer</span>
    <svg class="abs" style="left:337px;top:373px;" width="57" height="53" viewBox="0 0 57 53" fill="none" stroke="var(--icon)" stroke-width="2" stroke-linecap="round">
      <rect x="1" y="6" width="55" height="46" rx="5"/>
      <line x1="1" y1="16" x2="56" y2="16"/>
      <rect x="14" y="1" width="4" height="10" rx="1"/><rect x="39" y="1" width="4" height="10" rx="1"/>
      <path d="M17 27h22l-4-4M40 38H18l4 4"/>
    </svg>
    <p class="copy abs" style="left:40px;top:407px;">I would like to pay via monthly direct bank transfer.</p>
    <p class="copy abs" style="left:40px;top:439px;width:625px;">I understand that I am responsible for ensuring monthly payments are made on time in accordance with my agreed payment arrangement.</p>

    <h2 class="heading important-heading abs">Important</h2>
    <p class="copy abs" style="left:40px;top:531px;width:600px;">When making direct transfer payments, please use the <strong>patient's full name</strong> as the payment reference (for example: Jane Citizen), rather than the account holder's name. This ensures payments are correctly allocated to your treatment account.</p>
  </section>

  <section class="declaration">
    <h2 class="heading declaration-heading abs">Patient Declaration</h2>
    <p class="declaration-text abs">I have read and understood the payment options above and agree to my selected payment method.</p>
    <div class="sign-line abs" style="left:108px;top:738px;"></div>
    <span class="sign-label abs" style="left:108px;top:741px;">Signature</span>
    <div class="sign-line abs" style="left:475px;top:738px;"></div>
    <span class="sign-label abs" style="left:475px;top:741px;">Date</span>
  </section>

  <footer>
    <div class="footer-bank abs">
      <p class="footer-heading abs" style="left:41px;top:14px;">Our bank account details:</p>
      <div class="bank-row" style="top:33px;"><span class="key">Account Name</span><span class="val">: Northline Orthodontics</span></div>
      <div class="bank-row" style="top:52px;"><span class="key">Bank</span><span class="val">: Harbour Bank</span></div>
      <div class="bank-row" style="top:71px;"><span class="key">BSB</span><span class="val">: 000 123</span></div>
      <div class="bank-row" style="top:91px;"><span class="key">Account Number</span><span class="val">: 12345678</span></div>
    </div>
    <div class="footer-info abs">
      <p class="footer-heading info-heading abs">Information:</p>
      <div class="info-row" style="top:33px;"><svg viewBox="0 0 12 12" fill="none" stroke="var(--blue)"><path d="M6 11s4-3.8 4-6.5a4 4 0 0 0-8 0C2 7.2 6 11 6 11z"/><circle cx="6" cy="4.5" r="1.4"/></svg>48 Harbour Rd, Eastvale VIC 3100</div>
      <div class="info-row" style="top:52px;"><svg viewBox="0 0 12 12" fill="none" stroke="var(--blue)"><path d="M2 1.5l2 0 1 3-1.3 1a6 6 0 0 0 2.8 2.8l1-1.3 3 1v2A1 1 0 0 1 9.5 11 9 9 0 0 1 1 2.5a1 1 0 0 1 1-1z"/></svg>03 9000 1234</div>
      <div class="info-row" style="top:70px;"><svg viewBox="0 0 12 12" fill="none" stroke="var(--blue)"><rect x="1.5" y="4" width="9" height="7" rx="1"/><path d="M3.5 4V1h5v3M3.5 7h5M3.5 9h5"/></svg>03 9000 5678</div>
      <div class="info-row" style="top:88px;"><svg viewBox="0 0 12 12" fill="none" stroke="var(--blue)"><rect x="1" y="2.5" width="10" height="7"/><path d="M1 2.5l5 4 5-4"/></svg>eastvale@northline-ortho.com.au</div>
      <div class="footer-divider abs"></div>
      <p class="footer-heading abs" style="left:255px;top:14px;color:var(--ink);">Registered Specialist Orthodontists:</p>
      <div class="doctor" style="top:33px;"><svg viewBox="0 0 12 14" fill="none" stroke="var(--blue)"><path d="M3 1c-2 0-2 3-1.5 5S2.5 13 3.5 13 5 8 6 8s1.5 5 2.5 5 1.5-5 2-7S11 1 9 1 7 2 6 2 5 1 3 1z"/></svg><div><strong>Dr Hannah Reyes</strong>MDSc, Grad Dip Clin Dent, BDSc(Hons)</div></div>
      <div class="doctor" style="top:59px;"><svg viewBox="0 0 12 14" fill="none" stroke="var(--blue)"><path d="M3 1c-2 0-2 3-1.5 5S2.5 13 3.5 13 5 8 6 8s1.5 5 2.5 5 1.5-5 2-7S11 1 9 1 7 2 6 2 5 1 3 1z"/></svg><div><strong>Dr Owen Marsh</strong>MDSc, Grad Dip Clin Dent, MOrth, BDSc</div></div>
      <div class="doctor" style="top:85px;"><svg viewBox="0 0 12 14" fill="none" stroke="var(--blue)"><path d="M3 1c-2 0-2 3-1.5 5S2.5 13 3.5 13 5 8 6 8s1.5 5 2.5 5 1.5-5 2-7S11 1 9 1 7 2 6 2 5 1 3 1z"/></svg><div><strong>Dr Lucas Tran</strong>DCD, MOrth, MRACDS (Orth), BDSc (Hons)</div></div>
    </div>
  </footer>
</main>
</body>
</html>
```